menu board design: rustle burger

we are a burger restaurant.
we need to re design our menu board to fit within the new design of the restaurant. we are after something simple and easy to read. the overall look and feel of the design should be inline with the design of the shop.

Target Market(s)

18-40 male and female

Colors

Designer to choose colors to be used in the design.

Requirements
Must have
• easy to read. good layout. white background. branding included in design.

```html
<!DOCTYPE html>
<html lang="en">
<head>
<meta charset="utf-8">
<title>Rustle Burger – Menu Board</title>
<link rel="stylesheet" href="https://fonts.googleapis.com/css2?family=Oswald:wght@600;700&family=Signika:wght@300;400;600&family=Montserrat:wght@500&display=swap">
<style>
  :root{
    --frame:#cfdbe8;
    --paper:#ffffff;
    --navy:#1d4e8f;
    --gold:#d9b52a;
    --gold-text:#d4ad24;
    --wine:#8e1f34;
    --ink:#2a2a2a;
  }
  *{box-sizing:border-box;margin:0;padding:0}
  html,body{width:1200px;height:600px;overflow:hidden;background:var(--frame)}
  .board{position:relative;width:1200px;height:600px;background:var(--frame);font-family:"Signika",sans-serif;color:var(--ink)}
  .panel{position:absolute;left:33px;top:30px;width:1134px;height:537px;background:var(--paper);border-radius:30px}
  .abs{position:absolute}
  .banner{position:absolute;background:var(--gold);display:flex;align-items:center;justify-content:center;
    font-family:"Oswald",sans-serif;font-weight:700;color:var(--navy);letter-spacing:.5px;line-height:1}
  .banner--wine{color:var(--wine)}
  .intro{font-weight:300;font-size:11px;line-height:14.4px;text-align:center}
  .patty{font-weight:600;font-size:11.5px;color:var(--navy);text-align:center;letter-spacing:.3px}
  .item{position:absolute}
  .item__head{display:flex;align-items:baseline;font-weight:600;font-size:12px;color:var(--gold-text);letter-spacing:.2px;line-height:14px}
  .item__dots{flex:1;border-bottom:1.5px dotted var(--gold-text);margin:0 2px;transform:translateY(-3px)}
  .item__desc{font-weight:300;font-size:10px;line-height:13px;margin-top:2px;text-align:justify}
  .brand{position:absolute;left:468px;top:50px;width:256px;text-align:center;font-family:"Signika",sans-serif;font-weight:600;color:var(--navy);font-size:62px;line-height:70px}
  .tagline{position:absolute;left:468px;top:279px;width:256px;font-family:"Montserrat",sans-serif;font-weight:500;font-size:13px;letter-spacing:4.6px;color:var(--navy);text-align:center;padding-bottom:4px;border-bottom:2px solid var(--navy)}
  .rule{position:absolute;height:0;border-top:2px dashed var(--navy)}
  .step{position:absolute;background:var(--gold);color:var(--navy);font-weight:600;font-size:11px;display:flex;align-items:center;justify-content:center}
  .choose{position:absolute;font-weight:600;font-size:11.5px;color:var(--navy);text-align:center;letter-spacing:.3px}
  .gold-copy{font-weight:300;font-size:10.5px;line-height:14.4px;color:var(--gold-text);text-align:justify}
  .gold-copy b{font-weight:600}
  .side-line{font-size:14.5px;line-height:18px}
  .art{position:absolute;border-radius:6px}
  .sauce{position:absolute;font-weight:600;font-size:11.5px;line-height:14.4px;color:var(--navy)}
</style>
</head>
<body>
<main class="board">
  <div class="panel"></div>

  <!-- Beef burgers -->
  <h2 class="banner" style="left:120px;top:35px;width:207px;height:31px;font-size:28px">BEEF BURGERS</h2>
  <p class="intro abs" style="left:69px;top:70px;width:315px">All our patties are 100% natural beef. We know because we grind it ourselves, smashed to order on a hot grill rite in from of you</p>
  <p class="patty abs" style="left:69px;top:123px;width:315px">DOUBLE PATTY ADD 4</p>

  <div class="item" style="left:67px;top:141px;width:312px">
    <div class="item__head"><span>CLASSIC BEEF</span><span class="item__dots"></span><span>8.9</span></div>
    <p class="item__desc">Shredded lettuce, sliced tomato, caramelised onions, beetroot and BBQ sauce on a buttered sesame seed bum.</p>
  </div>
  <div class="item" style="left:67px;top:193px;width:312px">
    <div class="item__head"><span>CHEESE BURGER</span><span class="item__dots"></span><span>9.5</span></div>
    <p class="item__desc">Dill pickles, minced onion, american cheese, mustard and ketchup on soft milk bun.</p>
  </div>
  <div class="item" style="left:67px;top:240px;width:312px">
    <div class="item__head"><span>FLAME GRILL</span><span class="item__dots"></span><span>9.5</span></div>
    <p class="item__desc">Shredded lettuce, sliced tomato, minced onion, dill pickles, american cheese, mayo and ketchup on a soft bun.</p>
  </div>
  <div class="item" style="left:67px;top:288px;width:312px">
    <div class="item__head"><span>BIG STACK</span><span class="item__dots"></span><span>9.9</span></div>
    <p class="item__desc">Shredded lettuce, dil pickles, minced onion, american cheese and special sauce on a soft milk bun.</p>
  </div>

  <!-- Brand -->
  <h1 class="brand">Rustle<br>Burger</h1>
  <p class="tagline">CLASSICS FOR A REASON</p>

  <!-- Chicken burgers -->
  <h2 class="banner" style="left:816px;top:35px;width:267px;height:31px;font-size:28px">CHICKEN BURGERS</h2>
  <p class="intro abs" style="left:809px;top:70px;width:317px">All our patties are 100% natural beef. We know because we grind it ourselves, smashed to order on a hot grill rite in from of you</p>
  <p class="patty abs" style="left:809px;top:122px;width:317px">DOUBLE PATTY ADD 4</p>

  <div class="item" style="left:811px;top:140px;width:313px">
    <div class="item__head"><span>CLASSIC BEEF</span><span class="item__dots"></span><span>8.9</span></div>
    <p class="item__desc">Shredded lettuce, sliced tomato, caramelised onions, beetroot and BBQ sauce on a buttered sesame seed bum.</p>
  </div>
  <div class="item" style="left:811px;top:192px;width:313px">
    <div class="item__head"><span>CHEESE BURGER</span><span class="item__dots"></span><span>9.5</span></div>
    <p class="item__desc">Dill pickles, minced onion, american cheese, mustard and ketchup on soft milk bun.</p>
  </div>
  <div class="item" style="left:811px;top:239px;width:313px">
    <div class="item__head"><span>FLAME GRILL</span><span class="item__dots"></span><span>9.5</span></div>
    <p class="item__desc">Shredded lettuce, sliced tomato, minced onion, dill pickles, american cheese, mayo and ketchup on a soft bun.</p>
  </div>
  <div class="item" style="left:811px;top:287px;width:313px">
    <div class="item__head"><span>TRUFFLED</span><span class="item__dots"></span><span>9.9</span></div>
    <p class="item__desc">Rocket, caramelised onion, dill pickles, havarti cheese and truffle infused mayo on a soft milk bun.</p>
  </div>

  <!-- Dividers -->
  <div class="rule" style="left:92px;top:351px;width:376px"></div>
  <div class="rule" style="left:718px;top:351px;width:362px"></div>

  <!-- Nachos & loaded fries -->
  <h2 class="banner banner--wine" style="left:117px;top:366px;width:230px;height:29px;font-size:21px">NACHOS &amp; LOADED FRIES</h2>
  <div class="step" style="left:117px;top:423px;width:74px;height:17px">STEP ONE</div>
  <div class="step" style="left:292px;top:423px;width:74px;height:17px">STEP TWO</div>
  <p class="choose" style="left:85px;top:452px;width:140px">CHOOSE EITHER,</p>
  <p class="choose" style="left:262px;top:452px;width:140px">CHOOSE ONE,</p>

  <div class="item" style="left:65px;top:481px;width:179px">
    <div class="item__head"><span>SEASONED FRIES</span><span class="item__dots"></span><span style="font-weight:300">9.9</span></div>
  </div>
  <div class="item" style="left:65px;top:510px;width:179px">
    <div class="item__head"><span>OR FRESHLY COOKED</span></div>
    <div class="item__head" style="margin-top:1px"><span>CORN CHIPS</span><span class="item__dots"></span><span style="font-weight:300">11.5</span></div>
  </div>
  <p class="gold-copy abs" style="left:252px;top:481px;width:162px"><b>GUACAMOLE</b> salsa fresca, guacamole, jalapeñoz, cheese sauce and sour cream. <b>BEEF CHILLI</b> salsa fresca, beef chilli, jalapeños, cheese sauce and sour cream.</p>

  <!-- Sides -->
  <h2 class="banner" style="left:527px;top:337px;width:135px;height:39px;font-size:33px">SIDES</h2>
  <div class="item" style="left:483px;top:395px;width:219px">
    <div class="item__head side-line"><span>FRIES</span><span class="item__dots"></span><span>3.5</span></div>
    <div class="item__head side-line"><span>SOUTHERN TENDERS</span><span class="item__dots"></span><span>6.9</span></div>
  </div>
  <p class="abs" style="left:483px;top:444px;width:225px;font-weight:300;font-size:10.5px;line-height:13px">Breaded and fried chicken tenders with secret seasoning. <b style="font-weight:600">(2 PCS).</b></p>
  <div class="art" role="img" aria-label="Sketch of a burger" style="left:495px;top:498px;width:108px;height:63px;background:linear-gradient(#e4ebf3,#c9d7e7)"></div>
  <div class="art" role="img" aria-label="Sketch of an iced drink" style="left:627px;top:474px;width:54px;height:87px;background:linear-gradient(#e4ebf3,#c9d7e7)"></div>

  <!-- Buffalo chicken ribs -->
  <h2 class="banner banner--wine" style="left:831px;top:367px;width:230px;height:29px;font-size:21px">BUFFALO CHICKEN RIBS</h2>
  <p class="abs" style="left:782px;top:415px;width:340px;text-align:center;font-weight:300;font-size:10.5px;line-height:13px">Buffalo style fried chicken ribs smothered in one dur mouth-watering sauce. Served with a side of ranch sauce.</p>

  <div class="item" style="left:792px;top:469px;width:158px">
    <div class="item__head"><span>6 PACK</span><span class="item__dots"></span><span style="font-weight:300">6.9</span></div>
  </div>
  <div class="item" style="left:792px;top:498px;width:158px">
    <div class="item__head"><span>12 PACK</span><span class="item__dots"></span><span style="font-weight:300">12.9</span></div>
  </div>
  <div class="item" style="left:792px;top:526px;width:158px">
    <div class="item__head"><span>24 PACK</span><span class="item__dots"></span><span style="font-weight:300">23.9</span></div>
  </div>
  <p class="sauce" style="left:986px;top:485px">CLASSIC HOT SAUCE<br>OR SMOKY BBQ</p>
</main>
</body>
</html>
```